Silver Kite Venture Series Travel Brochure

I'm looking for a brochure design for a new travel product - Silver Kite Venture Series, catering for students above 12 years old. Target audience are schools that do destination projects. Brochure to be read by head teacher, parents and students.

Brochure should be A4 in size, 4-6 pages. Format of brochure is hard cover (a folder) with inlet for flyers. Flyers for destinations will be updated from time to time.

Finished job needs to be converted to electronic format for website and email proposal usage.

Attached is text to be used on brochure. Order of section can be adjusted.

For "Elements of the trip", please understand the contents and explain/display it in a graphic form.

For flyer, please come out with a template that I can use for other destinations. The main elements - what's included, number of days, location for pictures, itinerary, educational focus, should be alterable. Attached are text for two sample destinations.
Also attached (tour itinerary example) a version of flyer that I like.

I'm attaching some pictures here. If you find more suitable pictures, please feel free to use them.

Reason: I'm extending the deadline of this project by 4 days, as I need to add details & photo of another travel specialist in personnel session (total of 3 members). Also, in view of the amount of work a designer has to do for this project, I'm giving you more time for submission. Please do not hesitate to be in touch should you need more than 4 days extension. Thank you.

Target Market(s)

Schools - especially the head teacher and parents, to send students above 12 years old to travel

Industry/Entity Type

Electronic

Requirements
Must have
• This is a travel brochure with education elements in it. Parents feel better when their children are travelling for a purpose and lead by responsible teachers/adults whom they can trust. So, the design has to emphasis that education elements and safety are our utmost priority.
Nice to have
• We specialise in environmental study. So, it is nice to have the environmental touch in the design.
Should not have
• Our target market segment is the Middle East, which can be quite sensitive to religion. I prefer not to have any religious related illustration on the design.

```html
<!DOCTYPE html>
<html lang="en">
<head>
<meta charset="utf-8">
<title>Silver Kite Venture Series – Destination Flyer</title>
<link rel="stylesheet" href="https://fonts.googleapis.com/css2?family=Alfa+Slab+One&family=Open+Sans:wght@400;600&family=Source+Sans+3:wght@300;400&display=swap">
<style>
  :root {
    --page: #ffffff;
    --navy: #1d3a6b;
    --title-blue: #2c5ea8;
    --panel-green: #9cc93b;
    --heading-green: #3f9a35;
    --stem: #3fa03a;
    --leaf-light: #b5dc6a;
    --leaf-mid: #7fc241;
    --sky: #5ca4da;
    --ink: #1e1e1e;
    --day: #eef9cf;
    --white: #ffffff;
  }
  * { box-sizing: border-box; margin: 0; padding: 0; }
  html, body { width: 864px; height: 1200px; overflow: hidden; background: var(--page); }
  body { position: relative; font-family: "Open Sans", Arial, sans-serif; color: var(--ink); }

  .brand { position: absolute; left: 42px; top: 58px; display: flex; align-items: center; gap: 8px; }
  .brand-mark { width: 14px; height: 14px; background: var(--navy); }
  .brand-name { font-family: "Source Sans 3", Arial, sans-serif; font-weight: 400; font-size: 17px; color: var(--navy); letter-spacing: 0.3px; }

  .series-title {
    position: absolute; left: 224px; top: 48px; z-index: 3;
    font-family: "Source Sans 3", Arial, sans-serif; font-weight: 300;
    font-size: 44px; color: var(--title-blue); line-height: 1; white-space: nowrap;
  }

  .destination { position: absolute; left: 42px; width: 782px; }
  .destination--malaysia { top: 110px; height: 514px; --itin-h: 249px; --focus-h: 167px; }
  .destination--greece { top: 664px; height: 496px; --itin-h: 233px; --focus-h: 169px; }

  .photo { position: absolute; left: 0; top: 0; width: 260px; height: 100%; }
  .destination--malaysia .photo { background: linear-gradient(180deg, #c3d6e8 0%, #7d97ad 22%, #4a6557 42%, #3d6b2d 68%, #243f1a 100%); }
  .destination--greece .photo { background: linear-gradient(135deg, #2f6fb3 0%, #4d8fcc 30%, #c9b89c 55%, #b3a07f 80%, #8f7d60 100%); }

  .photo-label { position: absolute; left: 0; width: 260px; text-align: center; color: var(--white); font-family: "Alfa Slab One", Georgia, serif; }
  .photo-label .number { display: block; font-size: 18px; line-height: 1.2; }
  .photo-label .place { display: block; font-size: 40px; line-height: 1.05; }
  .destination--malaysia .photo-label { top: 264px; }
  .destination--greece .photo-label { top: 212px; }

  .itinerary { position: absolute; left: 260px; top: 0; width: 522px; height: var(--itin-h); background: var(--panel-green); display: flex; padding: 41px 0 0 28px; }
  .itinerary-col { width: 247px; }
  .day { font-family: "Alfa Slab One", Georgia, serif; font-size: 12px; line-height: 15.5px; color: var(--day); }
  .stop { font-size: 11.5px; line-height: 15.5px; color: var(--ink); }

  .focus { position: absolute; left: 260px; top: var(--itin-h); width: 522px; height: var(--focus-h); background: var(--sky); display: flex; padding: 16px 0 0 28px; }
  .focus-col { width: 247px; padding-right: 38px; }
  .focus h3 { font-family: "Alfa Slab One", Georgia, serif; font-weight: 400; font-size: 17.5px; line-height: 24px; color: var(--navy); }
  .focus p { font-weight: 600; font-size: 13px; line-height: 18.5px; color: var(--white); margin-bottom: 4px; }

  .included { position: absolute; left: 260px; top: calc(var(--itin-h) + var(--focus-h)); width: 522px; padding: 8px 0 0 28px; }
  .included h3 { font-family: "Alfa Slab One", Georgia, serif; font-weight: 400; font-size: 17.5px; line-height: 24px; color: var(--heading-green); margin-bottom: 4px; }
  .included ul { list-style: none; columns: 2; column-gap: 0; width: 494px; }
  .included li { font-size: 12.5px; line-height: 18.5px; }

  .stem { position: absolute; left: 258px; top: 6px; width: 4px; bottom: -6px; background: var(--stem); z-index: 2; }
  .leaf-area {
    position: absolute; left: 185px; top: -26px; width: 291px; height: 66px; z-index: 2;
    border-radius: 4px;
    background: linear-gradient(90deg, var(--stem) 0%, var(--leaf-mid) 30%, var(--leaf-light) 100%);
  }
</style>
</head>
<body>
  <div class="brand">
    <span class="brand-mark"></span>
    <span class="brand-name">Northfield Advisory</span>
  </div>
  <h1 class="series-title">Silver Kite Venture Series</h1>

  <section class="destination destination--malaysia">
    <div class="photo" role="img" aria-label="Photograph of misty mountains and rainforest in Borneo"></div>
    <div class="photo-label"><span class="number">Destination 1</span><span class="place">MALAYSIA<br>BORNEO</span></div>

    <div class="itinerary">
      <div class="itinerary-col">
        <p class="day">Day 1</p><p class="stop">Arrival at Kota Kinabalu<br>Cultural performance dinner</p>
        <p class="day">Day 2</p><p class="stop">Kiulu river rafting<br>Village visit</p>
        <p class="day">Day 3</p><p class="stop">Kinabalu Park trekking<br>Poring Hot Spring visit</p>
        <p class="day">Day 4</p><p class="stop">Sabah tea visit<br>Sukau Kinabatangan wildlife cruise</p>
      </div>
      <div class="itinerary-col">
        <p class="day">Day 5</p><p class="stop">Sepilok Orang Utan Rehabilitation<br>Center visit<br>Sandakan city tour</p>
        <p class="day">Day 6</p><p class="stop">Fly to Kuala Lumpur<br>City tour<br>School visit (optional)</p>
        <p class="day">Day 7</p><p class="stop">Departure</p>
      </div>
    </div>

    <div class="focus">
      <div class="focus-col">
        <h3>Main focus subject</h3><p>Environmental Management</p>
        <h3>Related subjects</h3><p>Geography, Development Studies, Agriculture, Physical Education</p>
      </div>
      <div class="focus-col">
        <h3>Environmental focus</h3><p>Biodiversity of Malaysian rainforests and conservation projects.</p>
      </div>
    </div>

    <div class="included">
      <h3>What's included in price:</h3>
      <ul>
        <li>Air ticket</li><li>All accommodation</li><li>Full time tour director</li>
        <li>Meals</li><li>Tours led by local expert tour guides</li><li>Entrance fees to attractions</li>
      </ul>
    </div>

    <div class="stem"></div>
    <div class="leaf-area" role="img" aria-label="Decorative green leaf growing from the stem"></div>
  </section>

  <section class="destination destination--greece">
    <div class="photo" role="img" aria-label="Photograph of an ancient stone column against a blue sky"></div>
    <div class="photo-label"><span class="number">Destination 2</span><span class="place">GREECE</span></div>

    <div class="itinerary">
      <div class="itinerary-col">
        <p class="day">Day 1</p><p class="stop">Arrival at Athens<br>Athens city tour</p>
        <p class="day">Day 2</p><p class="stop">Athens to Mykonos on cruise<br>Mykonos tour</p>
        <p class="day">Day 3</p><p class="stop">Mykonos to Kusadasi (Turkey) on cruise<br>Kusadasi tour</p>
        <p class="day">Day 4</p><p class="stop">Kusadasi to Santorini on cruise<br>Santorini and volcano tour</p>
      </div>
      <div class="itinerary-col">
        <p class="day">Day 5</p><p class="stop">Santorini to Athens on cruise<br>Athens second city tour</p>
        <p class="day">Day 6</p><p class="stop">Athens to Delphi by coach (2 hours)<br>Visit hill towns on way<br>Delphi tour</p>
        <p class="day">Day 7</p><p class="stop">Departure</p>
      </div>
    </div>

    <div class="focus">
      <div class="focus-col">
        <h3>Main focus subject</h3><p>Geography</p>
        <h3>Related subjects</h3><p>History, Anthropology, Environmental Management, Art and Design</p>
      </div>
      <div class="focus-col">
        <h3>Environmental focus</h3><p>Marine ecology and related human threats.</p>
      </div>
    </div>

    <div class="included">
      <h3>What's included in price:</h3>
      <ul>
        <li>Air ticket</li><li>All accommodation</li><li>Full time tour director</li>
        <li>Meals</li><li>Tours led by local expert tour guides</li><li>Entrance fees to attractions</li>
      </ul>
    </div>

    <div class="stem"></div>
    <div class="leaf-area" role="img" aria-label="Decorative green leaf growing from the stem"></div>
  </section>
</body>
</html>
```